Kelvara Pane Works Business Card

We need a business card design that is suitable for a Glazing Business. We Specialize in Repairing broken windows and doors and are a 24hr on call service. We manufacture Shower screens, Fly screens, Wardrobe doors, Security doors and grilles + mirrors. We stock a variety of mesh including Standard mesh, Pet resistant mesh, Tressmet & Clearweft. We would like to use a combination of Light Blue, Dark Blue, Black & White with perhaps a picture of glass breaking.

Industry/Entity Type

Business

Contact Information for Business Card

Narooma Glass Service60B Glasshouse Rocks RdNarooma NSW 2546PH / FAX - 02 44765210MOB - 0419682350 Andrewemail - kelvarapane@fenmail.example

Font styles to use
Serif

Colors
34a7d8
0255a3
ffffff

Requirements
Must have
• logo with picture of broken or cracked glass

```html
<!DOCTYPE html>
<html lang="en">
<head>
<meta charset="utf-8">
<title>Kelvara Pane Works Business Card</title>
<link rel="stylesheet" href="https://fonts.googleapis.com/css2?family=Source+Sans+3:wght@400;600&display=swap">
<style>
  :root {
    --backdrop: #141414;
    --card-white: #ffffff;
    --brand-light: #34a7d8;
    --brand-dark: #0255a3;
    --name-blue: #2e8fd0;
    --text-grey: #5a5a5a;
    --back-top: #5fcbe5;
    --back-bottom: #3b83c7;
    --back-mark: #4a9bd0;
    --back-text: #ffffff;
  }
  * { box-sizing: border-box; margin: 0; padding: 0; }
  html, body { width: 1200px; height: 900px; overflow: hidden; }
  body {
    background: var(--backdrop);
    font-family: "Source Sans 3", sans-serif;
    position: relative;
  }
  .card {
    position: absolute;
    top: 306px;
    width: 440px;
    height: 271px;
    border-radius: 12px;
  }
  .card-front { left: 149px; background: var(--card-white); }
  .card-back {
    left: 608px;
    background: linear-gradient(180deg, var(--back-top), var(--back-bottom));
  }
  .brand {
    position: absolute;
    left: 0; right: 0;
    display: flex;
    justify-content: center;
    align-items: center;
    gap: 12px;
  }
  .card-front .brand { top: 48px; --mark: var(--brand-light); }
  .card-back .brand { top: 70px; --mark: var(--back-mark); }
  .brand-symbol {
    width: 46px; height: 46px;
    border-radius: 50%;
    background: var(--mark);
    flex: none;
  }
  .wordmark {
    color: var(--mark);
    font-weight: 600;
    text-align: center;
  }
  .wordmark-name {
    display: block;
    font-size: 40px;
    line-height: 42px;
    letter-spacing: 5px;
    margin-right: -5px;
  }
  .wordmark-line {
    display: block;
    font-size: 21px;
    line-height: 28px;
    letter-spacing: 8px;
    margin-right: -8px;
  }
  .holder {
    position: absolute;
    right: 242px;
    top: 154px;
    text-align: right;
    color: var(--text-grey);
    font-size: 12.5px;
    line-height: 18px;
  }
  .holder-name {
    color: var(--name-blue);
    font-size: 17px;
    font-weight: 600;
    line-height: 18px;
    margin-bottom: 17px;
  }
  .contact-list {
    position: absolute;
    left: 219px;
    top: 152px;
    list-style: none;
    color: var(--text-grey);
    font-size: 12.5px;
    line-height: 18px;
  }
  .contact-list li { display: flex; align-items: center; gap: 7px; }
  .contact-list svg { width: 11px; height: 11px; fill: var(--brand-dark); flex: none; }
  .services {
    position: absolute;
    left: 0; right: 0;
    top: 178px;
    text-align: center;
    color: var(--back-text);
    font-weight: 600;
    font-size: 13px;
    line-height: 20px;
  }
  .services span::before {
    content: "";
    display: inline-block;
    width: 9px; height: 9px;
    border-radius: 50%;
    background: var(--back-text);
    opacity: .85;
    margin: 0 4px;
    vertical-align: -1px;
  }
</style>
</head>
<body>
  <section class="card card-front">
    <div class="brand">
      <div class="brand-symbol" role="img" aria-label="Cracked glass logo mark"></div>
      <div class="wordmark"><span class="wordmark-name">KELVARA</span><span class="wordmark-line">Pane Works</span></div>
    </div>
    <div class="holder">
      <div class="holder-name">Malcolm</div>
      <div>17C Tindale Ridge</div>
      <div>Rd Tindale NSW 2631</div>
    </div>
    <ul class="contact-list">
      <li><svg viewBox="0 0 12 12"><path d="M2.5 1l2 2-1 1.5c.7 1.5 2 2.8 3.5 3.5L8.5 7l2 2-1.5 2C5 10.5 1.5 7 1 3z"/></svg>02 48931067</li>
      <li><svg viewBox="0 0 12 12"><rect x="1" y="4" width="10" height="6" rx="1"/><rect x="3" y="1" width="6" height="3"/></svg>02 48931067</li>
      <li><svg viewBox="0 0 12 12"><rect x="3" y="0.5" width="6" height="11" rx="1"/></svg>0419682350</li>
      <li><svg viewBox="0 0 12 12"><path d="M1 2.5h10v7H1z M1 2.5l5 4 5-4" stroke="#fff" stroke-width=".8"/></svg>kelvarapane@fenmail.example</li>
    </ul>
  </section>

  <section class="card card-back">
    <div class="brand">
      <div class="brand-symbol" role="img" aria-label="Faint embossed cracked glass logo mark"></div>
      <div class="wordmark"><span class="wordmark-name">KELVARA</span><span class="wordmark-line">Pane Works</span></div>
    </div>
    <div class="services">
      <span>Shower screens</span> <span>Fly screens</span> <span>Wardrobe doors</span><br>
      Security doors <span>Grilles + mirrors</span>
    </div>
  </section>
</body>
</html>
```